Fern Moss Cleaning Tablets needs 4 x labels

We're about to launch a very exciting cleaning product to market and need your help to brand the 4 x bottles. www.fernmossly.com.au will change the way people buy and use household cleaning products whilst significantly reducing the impact on the earth.

The tablets are dropped into the long life recycled plastic bottle, you simply add water, wait for the tab to dissolve and begin cleaning.

Target Market(s)

Women aged between 30 - 65, care for the environment, want to use less plastic, are early adopters and like to try new things. Care about a clean home and using less chemicals. Want less packaging, less plastic, less carbon emissions.

Industry/Entity Type

House Cleaning

Font styles to use
Sans Serif

Requirements
Must have
• Each label must have an obvious colour differentiator and each label must be identical in it's dimensions and information. Should look uniform when all 4 bottles are aligned in the cupboard. Limited / no images apart from logo.
Nice to have
• Simple, clear, bold, striking. Limited / no pictures. Clean lines with lots of space.
Should not have
• Sparkwell Pane Label must have a strip of blue (hex BAE1FF).
Grime Hauler Kitchen Cleaner must have a strip of colour (FFD6F3)
The Fizzer Bathroom cleaner must have a colour strip hex # FFFFBA
The Allrounder Multip Purpose must have a strip of colour Hex #BAFFC9

```html
<!DOCTYPE html>
<html lang="en">
<head>
<meta charset="utf-8">
<title>The Allrounder – Multi Purpose Cleaner Label</title>
<link rel="stylesheet" href="https://fonts.googleapis.com/css2?family=Big+Shoulders+Display:wght@800;900&family=Questrial&family=Archivo:wght@800&display=swap">
<style>
  :root {
    --label-top: #fdfdfc;
    --label-bottom: #c3e1c1;
    --edge: #000000;
    --brand-teal: #12505e;
    --product-green: #62af98;
    --ink: #000000;
  }
  html, body {
    margin: 0;
    padding: 0;
    width: 1200px;
    height: 923px;
    overflow: hidden;
    background: #ffffff;
  }
  .label {
    display: block;
    width: 1200px;
    height: 923px;
  }
  .brand-name {
    font-family: "Questrial", sans-serif;
    font-size: 58px;
    fill: var(--brand-teal);
  }
  .brand-dot { fill: var(--brand-teal); }
  .product-name {
    font-family: "Questrial", sans-serif;
    font-size: 138px;
    fill: var(--product-green);
  }
  .product-type {
    font-family: "Big Shoulders Display", sans-serif;
    font-weight: 900;
    font-size: 164px;
    fill: var(--ink);
  }
  .tagline {
    font-family: "Questrial", sans-serif;
    font-size: 39px;
    fill: var(--ink);
  }
  .volume {
    font-family: "Archivo", sans-serif;
    font-weight: 800;
    font-size: 46px;
    fill: var(--ink);
  }
  .origin {
    font-family: "Big Shoulders Display", sans-serif;
    font-weight: 800;
    font-size: 36px;
    fill: var(--ink);
  }
</style>
</head>
<body>
<svg class="label" viewBox="0 0 1200 923" xmlns="http://www.w3.org/2000/svg">
  <defs>
    <linearGradient id="label-fill" x1="0" y1="0" x2="0" y2="1">
      <stop offset="0" stop-color="var(--label-top)" style="stop-color: var(--label-top)"/>
      <stop offset="1" stop-color="var(--label-bottom)" style="stop-color: var(--label-bottom)"/>
    </linearGradient>
  </defs>

  <rect class="label-body" x="4.5" y="1.5" width="1220" height="919" rx="70" ry="70"
        fill="url(#label-fill)" stroke="var(--edge)" stroke-width="3" style="stroke: var(--edge)"/>

  <g class="brand">
    <circle class="brand-dot" cx="370" cy="185" r="16"/>
    <text class="brand-name" x="628" y="205" text-anchor="middle">fernmossly.com.au</text>
  </g>

  <text class="product-name" x="618" y="410" text-anchor="middle"
        textLength="790" lengthAdjust="spacingAndGlyphs">The Allrounder</text>

  <text class="product-type" x="622" y="608" text-anchor="middle"
        textLength="909" lengthAdjust="spacingAndGlyphs">Multi Purpose Cleaner</text>

  <text class="tagline" x="608" y="706" text-anchor="middle"
        textLength="782" lengthAdjust="spacingAndGlyphs">One Bottle. One Tab. Dissolve. Clean. Repeat.</text>

  <text class="volume" x="620" y="778" text-anchor="middle">500 ml</text>

  <text class="origin" x="621" y="852" text-anchor="middle"
        textLength="276" lengthAdjust="spacingAndGlyphs">Seabrook. Australia</text>
</svg>
</body>
</html>
```